Federal IT Consulting Company - Brisolux Consulting Group

We're seeking a skilled web designer to create a modern, bold, and engaging WordPress website for Brisolux Consulting Group, LLC. Our company specializes in federal IT consulting, and our name is a play on "Brightening Solutions." The website should reflect our expertise in the federal technology marketplace and position us as a trusted partner for clients navigating their IT journey.

contact: info@brisoluxgrp-example.com

Current Status

WordPress is already installed on our hosting account
We have an existing logo (may need modernization)

Design Requirements

Style:

Modern and visually striking design
Bold elements to convey confidence and expertise
Incorporate the concept of "brightening solutions" into the design

Features:

Modern UX sliders for dynamic content presentation
Eye-catching, high-quality images (stock photos to be sourced by the designer)
Responsive design for all devices

Color Scheme:

To be proposed by the designer, should align with our brand and convey trust and technological expertise

Logo:

Evaluate our current logo
Create a transparent background version if needed
Propose modernization if deemed necessary

Accessibility:

Ensure design elements are accessible to users with disabilities
Use high contrast ratios for text and background colors
Provide text alternatives for non-text content

Website Structure
Create the following pages, with the possibility of subpages:

Home
Services
About
Contact

Specific Page Requirements
Home Page

Striking hero section with a clear value proposition
Overview of our services
Client testimonials or trust indicators

Services Page

Detailed list of our IT consulting services
Clear explanation of how we help navigate the federal IT landscape

About Page

Company history and mission
Team highlights (if applicable)
Our approach to federal IT consulting

Contact Page

Contact form
Other contact methods (phone, email)

Technical Requirements

Fully responsive design
SEO best practices implemented
Fast loading times
Integration with necessary plugins (to be discussed)
Training on how to update and maintain the site
Full compliance with Web Content Accessibility Guidelines (WCAG) 2.1 Level AA
Adherence to Section 508 standards for federal website accessibility
Implementation of necessary features for ADA compliance
Updates

Designs look the same

Target Market(s)

US Federal Govt customers looking for IT support.

Industry/Entity Type

IT Consulting

Coding

Coded - Design and coding required

Colors
0054AA
0677BA
7BADD7
CADEEF
E8F1F8
0094D4
00A9DD
6FCCEA
C7EBF8
E9F6FB
00AB8E
00BBA5
67D7C9
C6EFE9
E9F9F6

```html
<!DOCTYPE html>
<html lang="en">
<head>
<meta charset="utf-8">
<title>Brisolux Federal Services</title>
<link href="https://fonts.googleapis.com/css2?family=Orbitron:wght@700;800;900&family=Poppins:wght@300;400;500;600;700&display=swap" rel="stylesheet">
<style>
:root{
  --navy:#04152b;
  --navy-2:#0a2a4a;
  --ink:#111111;
  --blue:#0054AA;
  --blue-2:#0677BA;
  --sky:#0094D4;
  --cyan:#00A9DD;
  --cyan-soft:#6FCCEA;
  --mist:#E9F6FB;
  --text:#5c5c5c;
  --white:#ffffff;
  --head:'Orbitron',sans-serif;
  --body:'Poppins',sans-serif;
}
*{margin:0;padding:0;box-sizing:border-box}
html,body{width:1200px;height:3734px;overflow:hidden;background:var(--white);font-family:var(--body)}
.page{position:relative;width:1200px;height:3734px;overflow:hidden;
  background:linear-gradient(180deg,#fff 645px,#fff 900px,#eaf5fb 1300px,#fff 1600px)}
.abs{position:absolute}
.btn{position:absolute;display:flex;align-items:center;justify-content:center;border-radius:30px;
  background:linear-gradient(90deg,var(--cyan),var(--blue));color:#fff;font-weight:700;font-size:13px;letter-spacing:.3px;text-decoration:none}
.brand{font-family:var(--body);font-weight:700;color:#fff;letter-spacing:3px;display:flex;align-items:center;gap:12px}
.brand-dot{width:34px;height:34px;border-radius:50%;background:var(--cyan)}

/* hero */
.hero{position:absolute;left:0;top:0;width:1200px;height:645px;
  background:radial-gradient(ellipse at 30% 45%,#0b3a66 0%,#062443 40%,#03101f 100%);border-top:3px solid var(--sky)}
.hero-art{position:absolute;left:20px;top:150px;width:620px;height:440px;border-radius:50%;
  background:radial-gradient(ellipse at center,rgba(0,169,221,.55) 0%,rgba(0,84,170,.35) 45%,rgba(3,16,31,0) 72%)}
.nav{position:absolute;top:52px;left:493px;display:flex;gap:0;font-size:13px;color:#fff;font-weight:500}
.nav a{color:#fff;text-decoration:none;position:absolute;white-space:nowrap}
.nav .sep{position:absolute}
.hero-title{position:absolute;right:113px;top:232px;font-family:var(--head);font-weight:800;font-size:68px;color:#fff;letter-spacing:1px;text-align:right}
.hero-sub{position:absolute;right:113px;top:322px;font-weight:700;font-size:45px;color:#fff;text-align:right}
.hero-copy{position:absolute;right:113px;top:390px;width:480px;text-align:right;font-size:15px;line-height:32px;color:#fff}
.down{position:absolute;left:571px;top:616px;width:58px;height:58px;border-radius:50%;background:#fff;box-shadow:0 4px 12px rgba(0,0,0,.25);display:flex;align-items:center;justify-content:center}
.down span{width:40px;height:40px;border-radius:50%;background:linear-gradient(180deg,var(--cyan),var(--blue));display:flex;align-items:center;justify-content:center}

.intro{position:absolute;left:150px;top:750px;width:900px;text-align:center;color:var(--text);font-size:19px;line-height:39px}

/* about */
.h2{font-family:var(--head);font-weight:800;color:var(--ink);font-size:40px;letter-spacing:1px}
.about-h{position:absolute;left:112px;top:1052px}
.about-copy{position:absolute;left:112px;top:1118px;width:430px;font-size:14.5px;line-height:33px;color:var(--text)}
.photo-main{position:absolute;left:615px;top:985px;width:472px;height:472px;border-radius:50%;
  background:radial-gradient(circle at 40% 40%,#3a6fa8,#0c3a73 55%,#08234a)}
.photo-small{position:absolute;left:883px;top:1314px;width:198px;height:198px;border-radius:50%;border:5px solid #fff;
  background:radial-gradient(circle at 55% 35%,#f3a36a,#a9664f 35%,#3b5fa4 75%)}

/* services */
.services-bg{position:absolute;left:0;top:1613px;width:1200px;height:857px;
  background:radial-gradient(ellipse at 50% 30%,#2d8fd6 0%,#0b62c1 50%,#0750b0 100%)}
.services-h{position:absolute;left:0;width:1200px;top:1756px;text-align:center;color:#fff}
.services-copy{position:absolute;left:150px;width:900px;top:1819px;text-align:center;color:#fff;font-size:15.5px;line-height:31px}
.card{position:absolute;top:1924px;width:310px;height:365px;background:#fff;border-radius:22px;text-align:center}
.card svg{position:absolute;left:125px;top:45px}
.card h3{position:absolute;top:128px;width:100%;font-family:var(--head);font-weight:700;font-size:16px;color:var(--ink)}
.card p{position:absolute;top:164px;left:30px;width:250px;font-size:12.5px;line-height:25px;color:var(--text)}
.card .btn{left:86px;top:284px;width:138px;height:38px}

/* testimonials */
.test-h{position:absolute;left:112px;top:2588px}
.test-copy{position:absolute;left:112px;top:2653px;width:340px;font-size:14.5px;line-height:33px;color:var(--text)}
.arrow{position:absolute;top:2906px;width:38px;height:38px;border-radius:50%;background:linear-gradient(180deg,var(--cyan),var(--blue));color:#fff;display:flex;align-items:center;justify-content:center;font-size:14px;font-weight:700}
.quote{position:absolute;top:2562px;width:280px;height:426px;background:#fff;border-radius:30px;box-shadow:0 6px 24px rgba(0,84,170,.08);text-align:center}
.quote svg{position:absolute;left:120px;top:60px}
.quote p{position:absolute;top:113px;left:22px;width:236px;font-size:12.5px;line-height:29px;color:var(--text)}
.quote .name{position:absolute;top:325px;width:100%;color:var(--sky);font-weight:600;font-size:14px}
.quote .role{position:absolute;top:350px;width:100%;color:var(--ink);font-weight:500;font-size:13px}

.partners-h{position:absolute;left:0;width:1200px;top:3074px;text-align:center}
.partner{position:absolute;top:3168px;width:60px;height:60px;border-radius:50%}
.partner-card{position:absolute;left:514px;top:3166px;width:171px;height:109px;background:#fff;border-radius:8px;box-shadow:0 4px 18px rgba(0,0,0,.1)}

/* footer */
.footer{position:absolute;left:0;top:3354px;width:1200px;height:380px;background:#0c0c10}
.footer-links{position:absolute;top:3560px;left:0;width:1200px;font-size:16px;color:#fff;font-weight:500}
.footer-links span{position:absolute;white-space:nowrap}
.social{position:absolute;top:3610px;width:40px;height:40px;border-radius:50%;background:linear-gradient(180deg,var(--cyan),var(--blue))}
.copy{position:absolute;top:3670px;left:0;width:1200px;text-align:center;color:#fff;font-size:12px}
</style>
</head>
<body>
<div class="page">

  <header class="hero">
    <div class="hero-art" role="img" aria-label="Glowing digital compass over a dark blue technology background"></div>
    <div class="brand abs" style="left:113px;top:42px;font-size:30px"><span class="brand-dot"></span>BRISOLUX</div>
    <nav class="nav" style="left:0;top:54px;width:1200px">
      <a style="left:492px">HOME</a><span class="sep" style="left:563px">|</span>
      <a style="left:598px">SERVICES</a><span class="sep" style="left:693px">|</span>
      <a style="left:729px">ABOUT</a><span class="sep" style="left:806px">|</span>
      <a style="left:842px">CONTACT</a>
    </nav>
    <a class="btn" style="left:945px;top:42px;width:142px;height:41px">GET STARTED</a>
    <h1 class="hero-title">BRISOLUX</h1>
    <div class="hero-sub">FEDERAL SERVICES</div>
    <p class="hero-copy">Must explain to you how all this mistaken idea of denouncing pleasure and praising pain was born and I will give you a complete account of the system</p>
    <a class="btn" style="left:945px;top:510px;width:142px;height:41px">GET STARTED</a>
  </header>
  <div class="down"><span><svg width="14" height="18" viewBox="0 0 14 18"><path d="M7 1v14M2 10l5 6 5-6" stroke="#fff" stroke-width="2.2" fill="none"/></svg></span></div>

  <p class="intro">At vero eos et accusamus et iusto odio dignissimos ducimus qui blanditiis pr entium voluptatum deleniti atque corrupti quos dolores et quas molestias excepturi sint occaecati cupiditate non provident, similique sunt in culpa qui officia deserun</p>

  <section>
    <h2 class="h2 about-h">ABOUT US</h2>
    <p class="about-copy">I must explain to you how all this mistaken idea of denouncing pleasure and praising pain was born and I will give you a complete account of the system, and expound the actual teachings of the great explorer of the truth, the master-builder of human happiness. No one rejects, dislikes, or avoids pleasure itself, because it is pleasure, but because those</p>
    <a class="btn" style="left:112px;top:1372px;width:137px;height:37px">READ MORE</a>
    <svg class="abs" style="left:650px;top:965px" width="130" height="110" viewBox="0 0 130 110"><path d="M22 90A58 58 0 0 1 122 40" stroke="var(--blue-2)" stroke-width="22" fill="none"/></svg>
    <svg class="abs" style="left:635px;top:1390px" width="142" height="102" viewBox="0 0 142 102"><polygon points="0,4 140,4 71,100" fill="var(--ink)"/></svg>
    <div class="photo-main" role="img" aria-label="Two consultants in suits reviewing data on a digital screen"></div>
    <div class="photo-small" role="img" aria-label="Handshake in front of a city skyline at sunset"></div>
  </section>

  <section>
    <div class="services-bg" role="img" aria-label="Blue abstract network background"></div>
    <svg class="abs" style="left:0;top:1600px" width="1200" height="880" viewBox="0 1600 1200 880">
      <polygon points="601,1649 1200,1613 1200,1695" fill="var(--ink)"/>
      <polygon points="601,2384 1200,2470 0,2470" fill="#fff"/>
      <polygon points="0,2376 601,2384 0,2470" fill="var(--ink)"/>
    </svg>
    <h2 class="h2 services-h">OUR SERVICES</h2>
    <p class="services-copy">Sed ut perspiciatis unde omnis iste natus error sit voluptatem accusantium doloremque laudantium, totam rem aperiam, eaque ipsa quae ab illo inventore veritatis et quasi architecto beatae vitae dicta sunt</p>

    <div class="card" style="left:113px">
      <svg width="60" height="60" viewBox="0 0 60 60" fill="none" stroke="#1b2a3a" stroke-width="2"><circle cx="30" cy="30" r="17"/><circle cx="30" cy="30" r="8"/><path d="M30 5v8M30 47v8M5 30h8M47 30h8M12 12l6 6M42 42l6 6M48 12l-6 6M12 48l6-6"/></svg>
      <h3>DENOUNCING PLEASURE</h3>
      <p>Sed ut perspiciatis unde omnis iste natus error sit voluptatem accusantium doloremque laudantium, totam rem aperiam, eaque ipsa</p>
      <a class="btn">READ MORE</a>
    </div>
    <div class="card" style="left:445px">
      <svg width="60" height="60" viewBox="0 0 60 60" fill="none" stroke="#1b2a3a" stroke-width="2"><path d="M30 5l20 8v16c0 14-9 22-20 26C19 51 10 43 10 29V13z"/><path d="M30 5v50" /><circle cx="40" cy="30" r="6" stroke="var(--sky)"/></svg>
      <h3>DENOUNCING PLEASURE</h3>
      <p>Sed ut perspiciatis unde omnis iste natus error sit voluptatem accusantium doloremque laudantium, totam rem aperiam, eaque ipsa</p>
      <a class="btn">READ MORE</a>
    </div>
    <div class="card" style="left:777px">
      <svg width="60" height="60" viewBox="0 0 60 60" fill="none" stroke="#1b2a3a" stroke-width="2"><path d="M30 8l12 5v9c0 8-5 12-12 15-7-3-12-7-12-15v-9z" stroke="var(--sky)"/><path d="M6 46h12l10 4h14l12-8M18 46v10"/><circle cx="8" cy="10" r="3"/><circle cx="52" cy="10" r="3"/></svg>
      <h3>DENOUNCING PLEASURE</h3>
      <p>Sed ut perspiciatis unde omnis iste natus error sit voluptatem accusantium doloremque laudantium, totam rem aperiam, eaque ipsa</p>
      <a class="btn">READ MORE</a>
    </div>
  </section>

  <section>
    <h2 class="h2 test-h">TESTIMONIALS</h2>
    <div class="test-copy"><p>I must explain to you how all this mistaken idea of denouncing pleasure and praising pain was born and I will give you a complete accoun as born and I will give you</p><p style="margin-top:34px">Expound the actual teachings of the great explorer of the truth.</p></div>
    <div class="arrow" style="left:111px">&laquo;</div>
    <div class="arrow" style="left:159px">&raquo;</div>

    <div class="quote" style="left:501px">
      <svg width="40" height="34" viewBox="0 0 40 34" fill="#2c2c2c"><path d="M0 0h17v18l-6 16H3l5-14H0zM23 0h17v18l-6 16h-8l5-14h-8z"/></svg>
      <p>Sed ut perspiciatis unde omnis iste natus error sit voluptatem accusantium doloremque laudantium, totam rem aperiam, eaque ipsa quae ab illo inventore veritatis et quasi architecto beatae</p>
      <div class="name">DANA WHITFIELD</div>
      <div class="role">DNOUNCING PLEASURE &amp; PRAISING</div>
    </div>
    <div class="quote" style="left:807px">
      <svg width="40" height="34" viewBox="0 0 40 34" fill="#2c2c2c"><path d="M0 0h17v18l-6 16H3l5-14H0zM23 0h17v18l-6 16h-8l5-14h-8z"/></svg>
      <p>Sed ut perspiciatis unde omnis iste natus error sit voluptatem accusantium doloremque laudantium, totam rem aperiam, eaque ipsa quae ab illo inventore veritatis et quasi architecto beatae</p>
      <div class="name">DANA WHITFIELD</div>
      <div class="role">DNOUNCING PLEASURE &amp; PRAISING</div>
    </div>

    <h2 class="h2 partners-h">TRUSTED PARTNERS</h2>
    <div class="partner-card"></div>
    <div class="partner" style="left:216px;background:#e0463a;border-radius:12px"></div>
    <div class="partner" style="left:393px;background:#35b3a0"></div>
    <div class="partner" style="left:573px;top:3180px;background:#35a7d6"></div>
    <div class="partner" style="left:752px;background:#f2a51f"></div>
    <div class="partner" style="left:929px;background:#6bab3c;border-radius:12px"></div>
  </section>

  <footer>
    <div class="footer"></div>
    <svg class="abs" style="left:0;top:3354px" width="1200" height="110" viewBox="0 0 1200 110">
      <polygon points="0,0 1200,0 1200,37" fill="#fff"/>
      <polygon points="560,36 1200,36 1200,100" fill="var(--blue)"/>
    </svg>
    <div class="brand abs" style="left:0;width:1200px;justify-content:center;top:3478px;font-size:30px"><span class="brand-dot"></span>BRISOLUX</div>
    <div class="footer-links">
      <span style="left:314px">HOME</span><span style="left:397px">|</span>
      <span style="left:439px">OUR SERVICES</span><span style="left:587px">|</span>
      <span style="left:628px">ABOUT US</span><span style="left:743px">|</span>
      <span style="left:784px">CONTACT US</span>
    </div>
    <div class="social" style="left:529px" aria-label="Social link"></div>
    <div class="social" style="left:580px" aria-label="Social link"></div>
    <div class="social" style="left:631px" aria-label="Social link"></div>
    <p class="copy">(C) Copyright 2024 | All Rights Reserved</p>
  </footer>

</div>
</body>
</html>
```